The Molar Ledger (Cover Design for Ebook)

I need a cool and exciting eBook cover for my new book, launching very soon!
I want it to stand out and appeal to young professionals with big dreams.
It should be dramatic and bold and avoid cliche or generic photos. Simple design will work as long as it relates to the message of the book. The content will provide ten years of experience from working in the field and achieving success.
Title: The Molar Ledger (at the top)
(Subheading Updated) The secrets to money, motivation and success they don’t teach you in dental school
OR The secrets to success they don't teach you in dental school.
OR The secrets to money, motivation and success
(smaller under title)
Author Updated: Dr R Hollis (place at the bottom)
Updates

Target Market(s)

Ambitious young dentists
See instagram www.pictogrid.example/themolarledger for a sense of the style that I think could work.

Font styles to use
Serif
Sans Serif

Colors

Designer to choose colors to be used in the design.

Requirements
Must have
• Eye catching and cool.
• Show the benefits of success. Money, freedom, luxury
• Clear title and subheading
Nice to have
• Subtle dental reference
• dimensions 1600x2400
Should not have
• Boring photos of dentist/patients, dental clinic, teeth etc,

```html
<!DOCTYPE html>
<html lang="en">
<head>
<meta charset="utf-8">
<title>The Molar Ledger — Ebook Cover</title>
<link rel="stylesheet" href="https://fonts.googleapis.com/css2?family=Oswald:wght@300;400;500;600;700&display=swap">
<style>
  :root {
    --page-bg: #f2f2f2;
    --cover-bg: #050505;
    --frame-line: #333333;
    --ink: #ffffff;
    --photo-deep: #0a0e1a;
    --photo-mid: #1d2742;
    --photo-light: #46557a;
    --photo-shirt: #8d97b0;
  }
  html, body {
    margin: 0;
    padding: 0;
    width: 920px;
    height: 1200px;
    overflow: hidden;
    background: var(--page-bg);
  }
  .cover {
    position: absolute;
    left: 80px;
    top: 30px;
    width: 760px;
    height: 1140px;
    background: var(--cover-bg);
    color: var(--ink);
    font-family: 'Oswald', 'Arial Narrow', sans-serif;
    overflow: hidden;
  }
  .cover__frame {
    position: absolute;
    inset: 20px;
    border: 1.5px solid var(--frame-line);
    pointer-events: none;
  }
  .cover__title {
    position: absolute;
    top: 52px;
    left: 0;
    right: 0;
    margin: 0;
    text-align: center;
    text-transform: uppercase;
    line-height: 1;
  }
  .cover__title-main {
    display: block;
    font-weight: 600;
    font-size: 112px;
    letter-spacing: 1px;
  }
  .cover__title-sub {
    display: block;
    margin-top: 10px;
    font-weight: 500;
    font-size: 94px;
    letter-spacing: 26px;
    padding-left: 26px;
  }
  .cover__photo {
    position: absolute;
    top: 327px;
    left: 0;
    width: 760px;
    height: 522px;
    background:
      radial-gradient(ellipse 22% 60% at 52% 30%, rgba(141,151,176,0.55) 0%, rgba(141,151,176,0) 100%),
      radial-gradient(ellipse at 48% 55%, var(--photo-light) 0%, rgba(70,85,122,0) 60%),
      linear-gradient(180deg, var(--photo-mid) 0%, var(--photo-deep) 100%);
  }
  .cover__subtitle {
    position: absolute;
    top: 872px;
    left: 0;
    right: 0;
    margin: 0;
    text-align: center;
    text-transform: uppercase;
    font-weight: 300;
    font-size: 40px;
    line-height: 1.25;
    letter-spacing: 5px;
    padding-left: 5px;
  }
  .cover__author {
    position: absolute;
    top: 1060px;
    left: 0;
    right: 0;
    margin: 0;
    text-align: center;
    font-weight: 500;
    font-size: 36px;
    line-height: 1;
    letter-spacing: 7px;
    padding-left: 7px;
  }
</style>
</head>
<body>
  <main class="cover">
    <div class="cover__frame"></div>
    <h1 class="cover__title">
      <span class="cover__title-main">The Molar</span>
      <span class="cover__title-sub">Ledger</span>
    </h1>
    <div class="cover__photo" role="img" aria-label="Photo of a man in a navy suit and checked shirt tucking a stack of banknotes into his inside jacket pocket"></div>
    <p class="cover__subtitle">The secrets to money,<br>motivation and success</p>
    <p class="cover__author">Dr R Hollis</p>
  </main>
</body>
</html>
```